Business Card Design

We need a business card designed for our new company. Prefer a black card with white logo & writing.

Contact Information for Business Card

Ted Galloway, address: 7-4812 Fernhollow Road, Abbotsford, BC, V3K 8R2, Office Phone: 604-712-3390, Cell: 604-947-2164, Email: ted@resinworkshub.ca

Colors

Designer to choose only greyscale colors for use in the design.

```html
<!DOCTYPE html>
<html lang="en">
<head>
<meta charset="utf-8">
<title>Resin Works Hub – Business Card</title>
<link href="https://fonts.googleapis.com/css2?family=Poppins:wght@400;500;700&display=swap" rel="stylesheet">
<style>
  :root {
    --backdrop: #6f6f71;
    --card: #1d1d1e;
    --ink: #ffffff;
    --ink-soft: #e4e4e4;
    --front-mark: #2c2c2e;
  }
  * { margin: 0; padding: 0; box-sizing: border-box; }
  html, body {
    width: 900px; height: 1200px; overflow: hidden;
    background: var(--backdrop);
    font-family: "Poppins", sans-serif;
  }
  .card {
    position: absolute;
    width: 632px; height: 360px;
    background: var(--card);
  }
  .card--front { left: 134px; top: 212px; }
  .card--back  { left: 135px; top: 628px; }

  .front-mark {
    position: absolute; inset: 0;
    display: flex; flex-direction: column; align-items: center; justify-content: center;
    color: var(--front-mark);
    font-weight: 700; line-height: 1.05; text-align: center;
  }
  .front-mark .line-1 { font-size: 56px; }
  .front-mark .line-2 { font-size: 30px; letter-spacing: 14px; padding-left: 14px; margin-top: 6px; }

  .brand {
    position: absolute; left: 30px; top: 110px; width: 285px;
    display: flex; align-items: center; justify-content: center; gap: 12px;
    color: var(--ink);
  }
  .brand__square { width: 16px; height: 16px; background: var(--ink); flex: none; }
  .brand__name { font-weight: 700; line-height: 1.1; font-size: 34px; }
  .brand__name span { display: block; font-size: 20px; letter-spacing: 9px; margin-top: 4px; }

  .divider {
    position: absolute; left: 340px; top: 88px;
    width: 2px; height: 182px; background: var(--ink);
  }
  .details { position: absolute; left: 373px; top: 84px; color: var(--ink); }
  .details__name { font-size: 22px; font-weight: 700; letter-spacing: 0.3px; line-height: 1.2; }
  .details__role { font-size: 14px; color: var(--ink-soft); margin-top: 2px; }
  .details__address { font-size: 14px; color: var(--ink-soft); line-height: 1.5; margin-top: 8px; }
  .contacts { list-style: none; margin-top: 10px; }
  .contacts li {
    display: flex; align-items: center; gap: 8px;
    font-size: 14px; letter-spacing: 1.6px; line-height: 22px; color: var(--ink-soft);
  }
  .contacts li.plain { letter-spacing: 0.3px; }
  .contacts svg { width: 12px; height: 12px; flex: none; }
</style>
</head>
<body>
  <section class="card card--front" aria-label="Card front">
    <div class="front-mark">
      <div class="line-1">RESIN WORKS</div>
      <div class="line-2">HUB</div>
    </div>
  </section>

  <section class="card card--back" aria-label="Card back">
    <div class="brand">
      <div class="brand__square"></div>
      <div class="brand__name">RESIN WORKS<span>HUB</span></div>
    </div>

    <div class="divider"></div>

    <div class="details">
      <h1 class="details__name">TED GALLOWAY</h1>
      <p class="details__role">Manager</p>
      <p class="details__address">7-4812 Fernhollow Road,<br>Abbotsford, BC, V3K 8R2</p>
      <ul class="contacts">
        <li>
          <svg viewBox="0 0 24 24" fill="#fff"><path d="M6.6 10.8a15.2 15.2 0 0 0 6.6 6.6l2.2-2.2a1 1 0 0 1 1-.25 11.4 11.4 0 0 0 3.6.57 1 1 0 0 1 1 1V20a1 1 0 0 1-1 1A17 17 0 0 1 3 4a1 1 0 0 1 1-1h3.5a1 1 0 0 1 1 1c0 1.25.2 2.45.57 3.57a1 1 0 0 1-.25 1z"/></svg>
          604-712-3390
        </li>
        <li>
          <svg viewBox="0 0 24 24" fill="none" stroke="#fff" stroke-width="2.4"><rect x="6" y="2" width="12" height="20" rx="2"/><line x1="10" y1="18" x2="14" y2="18"/></svg>
          604-947-2164
        </li>
        <li class="plain">
          <svg viewBox="0 0 24 24" fill="#fff"><path d="M2 5h20v14H2z"/><path d="M2 5l10 8 10-8" fill="none" stroke="#1d1d1e" stroke-width="2"/></svg>
          ted@resinworkshub.ca
        </li>
        <li class="plain">
          <svg viewBox="0 0 24 24" fill="none" stroke="#fff" stroke-width="2.2"><circle cx="12" cy="12" r="10"/><ellipse cx="12" cy="12" rx="4.5" ry="10"/><line x1="2" y1="12" x2="22" y2="12"/></svg>
          www.resinworkshub.ca
        </li>
      </ul>
    </div>
  </section>
</body>
</html>
```